Meadowlight Soaps Business Card

The new business card design will incorporate my new logo components designed by one of your designers. Meadowlight Soaps creates high quality soaps and bath products. They would be suited for a Spa, Bed and Breakfast, Boutique environment. The look should be a white background.
Classy, soft and using the colour palet of the logo. The card will be two sided.

Reason: Need more time to make some changes and decide.

Target Market(s)

Looking to appeal to an upper end market. Spas, boutiques, independent gift stores, bridal salons, bed and breakfast, etc. I want the card to impart a sense of elegance, tranquility and Meadowlight. But also quality and value.

Industry/Entity Type

Business

Font styles to use
Sans Serif
Script

Requirements
Must have
• My logo on the front. But also on the back but faded out to allow written notes on the back.
On the front : Carol Pritchett
Owner/Creator
48 Fenwick Rd
Guelph, Ont N4K 2P9
519.402.6183
Creating Quality Handcrafted Soaps And Bath Products
Custom and Wholesale Orders Welcome
Www.meadowlightsoaps.ca
Www.folkbook.com / MeadowlightSoapandBath
info@meadowlightsoaps.ca

```html
<!DOCTYPE html>
<html lang="en">
<head>
<meta charset="utf-8">
<title>Meadowlight Soaps Business Card</title>
<link rel="stylesheet" href="https://fonts.googleapis.com/css2?family=Great+Vibes&family=Montserrat:wght@400;600;700&display=swap">
<style>
  :root {
    --backdrop: #2b2b2b;
    --card-white: #f7f7f5;
    --teal: #6fa89b;
    --teal-soft: #8fc2b5;
    --teal-back: #88bfb1;
    --ink: #5a5a5a;
    --ink-dark: #3a4a46;
    --dash: rgba(255,255,255,0.85);
  }
  * { box-sizing: border-box; margin: 0; padding: 0; }
  html, body { width: 1200px; height: 997px; overflow: hidden; }
  body {
    background: var(--backdrop);
    font-family: "Montserrat", sans-serif;
    position: relative;
  }
  .card {
    position: absolute;
    width: 520px;
    height: 297px;
    border-radius: 18px;
    overflow: hidden;
    box-shadow: 0 12px 30px rgba(0,0,0,0.45);
  }

  /* Back side */
  .card-back { left: 53px; top: 350px; background: var(--teal-back); }
  .card-back .notes-title {
    position: absolute; left: 0; width: 100%; top: 34px;
    text-align: center; font-weight: 700; font-size: 16px;
    color: var(--ink-dark); text-decoration: underline;
  }
  .card-back .notes-lines { position: absolute; left: 0; top: 0; }
  .faded-mark {
    position: absolute; left: 130px; top: 84px; width: 260px;
    opacity: 0.22; text-align: center;
  }
  .faded-mark .mark-dot {
    width: 80px; height: 80px; border-radius: 50%;
    background: #ffffff; margin: 0 auto 12px;
  }
  .faded-mark .mark-name {
    font-family: "Montserrat", sans-serif; font-weight: 600;
    font-size: 30px; color: #ffffff; line-height: 1;
  }

  /* Front side */
  .card-front { left: 627px; top: 350px; background: var(--card-white); }
  .card-front .band { position: absolute; left: 0; top: 0; }
  .owner { position: absolute; left: 50px; top: 26px; width: 260px; text-align: center; }
  .owner-name {
    font-family: "Great Vibes", cursive; font-size: 38px; font-weight: 400;
    color: var(--teal); line-height: 1;
  }
  .owner-role {
    font-size: 10px; font-weight: 600; letter-spacing: 0.5px;
    color: var(--ink); margin-top: 4px;
  }
  .brand { position: absolute; right: 26px; top: 46px; width: 180px; text-align: center; }
  .brand-dot {
    width: 58px; height: 58px; border-radius: 50%;
    background: var(--teal-soft); margin: 0 auto 8px;
  }
  .brand-name {
    font-family: "Montserrat", sans-serif; font-weight: 600;
    font-size: 20px; color: var(--teal); line-height: 1.1;
  }
  .orders {
    margin-top: 10px; font-size: 10px; font-weight: 600;
    color: var(--ink); line-height: 1.35; letter-spacing: 0.2px;
  }
  .contacts { position: absolute; left: 22px; top: 106px; list-style: none; }
  .contacts li {
    display: flex; align-items: center; gap: 10px;
    height: 25px; font-size: 11px; font-weight: 600; color: var(--ink);
  }
  .contacts svg { flex: none; }
  .tagline {
    position: absolute; left: 22px; bottom: 10px;
    font-size: 13px; font-weight: 700; color: #ffffff; letter-spacing: 0.2px;
  }
</style>
</head>
<body>

  <section class="card card-back" aria-label="Card back, notes side">
    <div class="faded-mark" role="img" aria-label="Faded Meadowlight Soaps logo">
      <div class="mark-dot"></div>
      <div class="mark-name">Meadowlight Soaps</div>
    </div>
    <p class="notes-title">Notes</p>
    <svg class="notes-lines" width="520" height="297" viewBox="0 0 520 297" aria-hidden="true">
      <g stroke="var(--dash)" stroke-width="1.6" stroke-dasharray="6 5">
        <line x1="60" y1="90" x2="460" y2="90"/>
        <line x1="60" y1="140" x2="460" y2="140"/>
        <line x1="60" y1="190" x2="460" y2="190"/>
        <line x1="60" y1="240" x2="460" y2="240"/>
      </g>
    </svg>
  </section>

  <section class="card card-front" aria-label="Card front">
    <svg class="band" width="520" height="297" viewBox="0 0 520 297" aria-hidden="true">
      <path d="M0 297 L0 258 L430 258 Q 495 258 520 222 L520 297 Z" fill="var(--teal)"/>
    </svg>

    <div class="owner">
      <h1 class="owner-name">Carol Pritchett</h1>
      <p class="owner-role">OWNER/CREATOR</p>
    </div>

    <div class="brand">
      <div class="brand-dot"></div>
      <p class="brand-name">Meadowlight Soaps</p>
      <p class="orders">Custom and Wholesale<br>Orders Welcome</p>
    </div>

    <ul class="contacts">
      <li>
        <svg width="20" height="20" viewBox="0 0 20 20" aria-hidden="true">
          <circle cx="10" cy="10" r="10" fill="var(--teal)"/>
          <path d="M6 7.5c0-1 .8-1.6 1.6-1.6h4.8c.8 0 1.6.6 1.6 1.6v.6h-2.2v-.8H8.2v.8H6z M7.2 9h5.6l1 4.5H6.2z" fill="#fff"/>
        </svg>
        <span>519.402.6183</span>
      </li>
      <li>
        <svg width="20" height="20" viewBox="0 0 20 20" aria-hidden="true">
          <circle cx="10" cy="10" r="10" fill="var(--teal)"/>
          <g fill="none" stroke="#fff" stroke-width="1.6">
            <rect x="5" y="8.5" width="6" height="3.6" rx="1.8" transform="rotate(-45 8 10.3)"/>
            <rect x="9" y="8" width="6" height="3.6" rx="1.8" transform="rotate(-45 12 9.8)"/>
          </g>
        </svg>
        <span>www.meadowlightsoaps.ca</span>
      </li>
      <li>
        <svg width="20" height="20" viewBox="0 0 20 20" aria-hidden="true">
          <circle cx="10" cy="10" r="10" fill="var(--teal)"/>
        </svg>
        <span>folkbook.com/MeadowlightSoapandBath</span>
      </li>
      <li>
        <svg width="20" height="20" viewBox="0 0 20 20" aria-hidden="true">
          <circle cx="10" cy="10" r="10" fill="var(--teal)"/>
          <rect x="5" y="6.5" width="10" height="7" rx="1" fill="#fff"/>
          <path d="M5.5 7l4.5 3.6L14.5 7" fill="none" stroke="var(--teal)" stroke-width="1.2"/>
        </svg>
        <span>info@meadowlightsoaps.ca</span>
      </li>
      <li>
        <svg width="20" height="20" viewBox="0 0 20 20" aria-hidden="true">
          <circle cx="10" cy="10" r="10" fill="var(--teal)"/>
          <path d="M10 4.5a3.6 3.6 0 0 1 3.6 3.6c0 2.6-3.6 7-3.6 7s-3.6-4.4-3.6-7A3.6 3.6 0 0 1 10 4.5z" fill="#fff"/>
          <circle cx="10" cy="8.1" r="1.3" fill="var(--teal)"/>
        </svg>
        <span>48 Fenwick Rd, Guelph, Ont N4K 2P9</span>
      </li>
    </ul>

    <p class="tagline">Creating Quality Handcrafted Soaps &amp; Bath Products</p>
  </section>

</body>
</html>
```